A clean crisp business card for a Landscape Construction company. Designed to be easy to read contact/ info and also be appealing/interesting, unlike a traditional business card.

Industry/Entity Type

Landscape Construction

Contact Information for Business Card

Company name : Brambleford Landscape Construction, phone number: (877) 62Vista, website:Bramblefordyards.example, Email, sales@bramblefordyards.example

Requirements
Nice to have
• Luxurious finishes/ details…. Icons or emblems next to contact info
Should not have
• Clipart or general pictures

```html
<!DOCTYPE html>
<html lang="en">
<head>
<meta charset="utf-8">
<title>Brambleford Landscape Construction – Business Card</title>
<link rel="stylesheet" href="https://fonts.googleapis.com/css2?family=Cinzel:wght@500&family=Arimo:wght@400&display=swap">
<style>
  :root {
    --backdrop: #3a3a3a;
    --card: #262626;
    --card-shade: #2c2c2c;
    --silver: #9a9a9a;
    --white: #f2f2f2;
    --blue: #1f6fd1;
    --green: #9ccc2e;
    --serif: 'Cinzel', Georgia, serif;
    --sans: 'Arimo', Arial, sans-serif;
  }
  * { box-sizing: border-box; margin: 0; padding: 0; }
  html, body { width: 1200px; height: 1015px; overflow: hidden; }
  body {
    background: var(--backdrop);
    display: flex;
    flex-direction: column;
    align-items: center;
    justify-content: center;
    gap: 50px;
  }
  .card {
    position: relative;
    width: 760px;
    height: 434px;
    background: radial-gradient(ellipse at 35% 40%, var(--card-shade), var(--card) 70%);
    overflow: hidden;
    box-shadow: 0 12px 30px rgba(0,0,0,.45);
  }
  .card__band {
    position: absolute;
    left: 0; right: 0; bottom: 0;
    height: 14px;
  }
  .card--front .card__band { background: var(--green); }
  .card--back .card__band { background: var(--blue); }

  /* Front */
  .front-name {
    position: absolute;
    inset: 0 0 14px 0;
    display: flex;
    flex-direction: column;
    align-items: center;
    justify-content: center;
    font-family: var(--serif);
    font-weight: 500;
    color: var(--silver);
    text-align: center;
  }
  .front-name__main { font-size: 62px; letter-spacing: 2px; line-height: 1; }
  .front-name__sub { font-size: 20px; letter-spacing: 9px; margin-top: 10px; }

  /* Back */
  .wordmark {
    position: absolute;
    top: 60px;
    right: 50px;
    display: flex;
    align-items: center;
    gap: 14px;
    font-family: var(--serif);
    font-weight: 500;
    color: var(--blue);
  }
  .wordmark__dot {
    width: 34px; height: 34px;
    border-radius: 50%;
    background: var(--green);
  }
  .wordmark__text { display: flex; flex-direction: column; line-height: 1; }
  .wordmark__main { font-size: 36px; letter-spacing: 1px; }
  .wordmark__sub { font-size: 11px; letter-spacing: 4.5px; margin-top: 6px; }

  .person {
    position: absolute;
    top: 110px;
    left: 48px;
  }
  .person__name {
    font-family: var(--serif);
    font-weight: 500;
    font-size: 34px;
    letter-spacing: 1px;
    line-height: 1;
  }
  .person__first { color: var(--blue); }
  .person__last { color: var(--green); }
  .person__role {
    font-family: var(--sans);
    font-size: 17px;
    color: var(--green);
    margin-top: 4px;
    letter-spacing: .5px;
  }

  .address {
    position: absolute;
    top: 190px;
    right: 50px;
    font-family: var(--sans);
    font-style: normal;
    font-size: 19px;
    color: var(--white);
    text-align: right;
    line-height: 1.3;
  }

  .contacts {
    position: absolute;
    left: 48px;
    bottom: 46px;
    list-style: none;
    font-family: var(--sans);
    font-size: 19px;
    color: var(--white);
  }
  .contacts__item {
    display: flex;
    align-items: center;
    gap: 10px;
    line-height: 1.45;
  }
  .contacts__icon { width: 18px; height: 18px; fill: none; stroke: var(--blue); stroke-width: 2; }
  .contacts__accent { color: var(--blue); }
</style>
</head>
<body>

  <section class="card card--front" aria-label="Card front">
    <h1 class="front-name">
      <span class="front-name__main">Brambleford</span>
      <span class="front-name__sub">LANDSCAPE CONSTRUCTION</span>
    </h1>
    <div class="card__band"></div>
  </section>

  <section class="card card--back" aria-label="Card back">
    <div class="wordmark">
      <span class="wordmark__dot"></span>
      <span class="wordmark__text">
        <span class="wordmark__main">Brambleford</span>
        <span class="wordmark__sub">LANDSCAPE CONSTRUCTION</span>
      </span>
    </div>

    <div class="person">
      <p class="person__name"><span class="person__first">CALDER</span> <span class="person__last">FINCH</span></p>
      <p class="person__role">MANAGING DIRECTOR</p>
    </div>

    <address class="address">
      421, Hollow Creek Road<br>45452, Country Name
    </address>

    <ul class="contacts">
      <li class="contacts__item">
        <svg class="contacts__icon" viewBox="0 0 24 24" aria-hidden="true"><path d="M5 3h4l2 5-2.5 1.5a11 11 0 0 0 6 6L16 13l5 2v4a2 2 0 0 1-2 2A16 16 0 0 1 3 5a2 2 0 0 1 2-2z"/></svg>
        (555) 010-4821
      </li>
      <li class="contacts__item">
        <svg class="contacts__icon" viewBox="0 0 24 24" aria-hidden="true"><rect x="3" y="5" width="18" height="14"/><path d="M3 5l9 8 9-8"/></svg>
        sales@bramblefordyards.example
      </li>
      <li class="contacts__item">
        <svg class="contacts__icon" viewBox="0 0 24 24" aria-hidden="true"><circle cx="12" cy="12" r="9"/><path d="M3 12h18M12 3c3 3 3 15 0 18M12 3c-3 3-3 15 0 18"/></svg>
        <span>www.<span class="contacts__accent">bramblefordyards</span>.example</span>
      </li>
    </ul>
    <div class="card__band"></div>
  </section>

</body>
</html>
```